Letter and Envelope Design For Harborline Realty

Please design a letter and an envelope incorporating our logo (See Attached). We are also launched a business card contest. Since we want them to match, please feel free to submit a design for both the business card and also the letter design and envelope.

Requirements
Must have
• The envelope, the letter and the business cards must match somehow connecting the designs. We want them to have something that holds them together besides the logo.

```html
<!DOCTYPE html>
<html lang="en">
<head>
<meta charset="utf-8">
<title>Harborline Realty Stationery</title>
<link rel="stylesheet" href="https://fonts.googleapis.com/css2?family=Source+Sans+3:wght@400;600;700&display=swap">
<style>
:root{
  --navy:#1a2494;
  --grey:#58585a;
  --ink:#3a3a3c;
  --paper:#fafafa;
  --bg:#e4e4e4;
}
*{margin:0;padding:0;box-sizing:border-box}
html,body{width:1200px;height:825px;overflow:hidden}
body{background:var(--bg);font-family:"Source Sans 3",sans-serif;color:var(--ink);position:relative}
.piece{position:absolute;background:var(--paper)}
.abs{position:absolute}
.ring{position:absolute;border-radius:50%;border:3px solid var(--navy)}
.seal{position:absolute;border-radius:50%;background:var(--grey);border:2px solid #fff;box-shadow:0 0 0 2px var(--grey)}
.brand{position:absolute;text-align:center;color:var(--navy);font-weight:600;text-transform:uppercase;line-height:1}
.brand .rule{display:inline-block;height:1px;background:var(--navy);vertical-align:middle}
.band{position:absolute;left:0;right:0;height:5px;background:linear-gradient(90deg,var(--navy),var(--grey))}
.contact{position:absolute;white-space:nowrap;display:flex;align-items:center;gap:3px}
.contact svg{fill:var(--navy)}

/* letter */
.letter{left:80px;top:78px;width:472px;height:668px}
.letter .greeting{left:38px;top:133px;font-size:11.5px;font-weight:700;color:#222}
.letter .body{left:39px;top:162px;width:395px;font-size:9.9px;line-height:12.4px;text-align:justify}
.letter .body p{margin-bottom:12.2px}
.letter .signature{left:36px;top:482px;width:74px;height:40px;background:linear-gradient(90deg,#d9d9d9,#eeeeee);border-radius:20px}
.letter .contact{font-size:7.6px;left:37px}

/* business card */
.card{top:276px;width:200px;height:114px}
.card-front{left:629px}
.card-back{left:851px}
.card .person{right:10px;top:40px;text-align:right;color:var(--navy);font-size:7px;font-weight:700;line-height:1.1}
.card .person span{display:block;color:var(--grey);font-size:5px;font-weight:400}
.card .contact{font-size:5px;left:12px}
.card .band{height:3px}
.card-back .web{left:0;right:0;top:103px;text-align:center;font-size:5.5px;color:var(--navy)}
.card-back .web .rule{display:inline-block;width:18px;height:1px;background:var(--navy);vertical-align:middle;margin:0 3px}

/* envelope */
.envelope{left:576px;top:442px;width:542px;height:304px}
.envelope .flap{position:absolute;left:0;top:0}
.envelope .front{position:absolute;left:0;top:68px;width:542px;height:236px;background:var(--paper)}
.envelope .address{left:50px;top:102px;font-size:7.3px;line-height:9.5px;display:flex;gap:4px}
</style>
</head>
<body>

<!-- Letterhead -->
<section class="piece letter">
  <div class="ring" style="left:75px;top:17px;width:42px;height:42px"></div>
  <div class="brand" style="left:40px;top:64px;width:112px;font-size:11px;letter-spacing:1px">Harborline<br>
    <span style="font-size:7.5px;letter-spacing:2.5px"><span class="rule" style="width:16px;margin-right:3px"></span>Realty<span class="rule" style="width:16px;margin-left:3px"></span></span>
  </div>

  <p class="abs greeting">Dear Mr. John,</p>
  <div class="abs body">
    <p>Lorem Ipsum is simply dummy text of the printing and typesetting industry. Lorem Ipsum has been the industry's standard dummy text ever since the 1500s, when an unknown printer took a galley of type and scrambled it to make a type specimen book. It has survived not only five centuries, but also the leap into electronic typesetting, remaining essentially unchanged.</p>
    <p>The standard chunk of Lorem Ipsum used since the 1500s is reproduced below for those interested. Sections 1.10.32 and 1.10.33 from "de Finibus Bonorum et Malorum" by Cicero are also reproduced in their exact original form, accompanied by English versions from the 1914 translation by H. Rackham</p>
    <p>Lorem Ipsum is simply dummy text of the printing and typesetting industry. Lorem Ipsum has been the industry's standard dummy text ever since the 1500s, when an unknown printer took a galley of type and scrambled it to make a type specimen book. It has survived not only five centuries, but also the leap into electronic typesetting, remaining essentially unchanged. It was popularised in the</p>
    <p>The standard chunk of Lorem Ipsum used since the 1500s is reproduced below for those interested. Sections 1.10.32 and 1.10.33 from "de Finibus Bonorum et Malorum" by Cicero are also reproduced in their exact original form, accompanied by English versions from the 1914 translation by H. Rackham</p>
    <p>The standard chunk of Lorem Ipsum used since the 1500s is reproduced below for those interested. Sections 1.10.32 and 1.10.33 from "de Finibus Bonorum et Malorum" by Cicero are also reproduced in their exact original form.</p>
  </div>
  <div class="abs signature" role="img" aria-label="Handwritten signature"></div>

  <div class="contact" style="top:627px">
    <svg width="7" height="7" viewBox="0 0 10 10"><path d="M2 0l2 2-1 2c1 1 2 2 3 3l2-1 2 2-2 2C4 10 0 6 0 2z"/></svg>555-014-2200&nbsp;
    <svg width="7" height="6" viewBox="0 0 10 8"><path d="M0 0h10v8H0z M0 0l5 4 5-4" /></svg>info@harborlinerealty.com&nbsp;
    <svg width="6" height="6" viewBox="0 0 10 10"><circle cx="5" cy="5" r="5"/></svg>www.harborlinerealty.com
  </div>
  <div class="band" style="top:639px"></div>
  <div class="seal" style="left:480px;top:698px;transform:translate(-501px,-719px) translate(501px,698px);left:0;top:0;display:none"></div>
  <div class="seal" style="left:500px;top:0;display:none"></div>
  <div class="seal" style="left:400px;top:620px;width:42px;height:42px"></div>
  <div class="contact" style="top:646px">
    <svg width="6" height="9" viewBox="0 0 10 14"><path d="M5 0a5 5 0 0 1 5 5c0 4-5 9-5 9S0 9 0 5a5 5 0 0 1 5-5zm0 3a2 2 0 1 0 0 4 2 2 0 0 0 0-4z"/></svg>Po. box 201, Street Name, City Name, Zip Code - 00000
  </div>
</section>

<!-- Business card, front -->
<section class="piece card card-front">
  <div class="ring" style="left:34px;top:8px;width:29px;height:29px;border-width:2px"></div>
  <div class="brand" style="left:10px;top:40px;width:78px;font-size:7.6px;letter-spacing:.7px">Harborline<br>
    <span style="font-size:5.5px;letter-spacing:1.8px"><span class="rule" style="width:10px;margin-right:2px"></span>Realty<span class="rule" style="width:10px;margin-left:2px"></span></span>
  </div>
  <div class="abs person">DANA ELLIS<span>President</span></div>
  <div class="contact" style="top:83px">
    <svg width="5" height="5" viewBox="0 0 10 10"><path d="M2 0l2 2-1 2c1 1 2 2 3 3l2-1 2 2-2 2C4 10 0 6 0 2z"/></svg>555-014-2200
  </div>
  <div class="contact" style="top:89px">
    <svg width="5" height="4" viewBox="0 0 10 8"><path d="M0 0h10v8H0z"/></svg>info@harborlinerealty.com
  </div>
  <div class="band" style="top:95px"></div>
  <div class="seal" style="left:169px;top:87px;width:19px;height:19px;border-width:1.5px;box-shadow:0 0 0 1.5px var(--grey)"></div>
  <div class="contact" style="top:101px">
    <svg width="4" height="6" viewBox="0 0 10 14"><path d="M5 0a5 5 0 0 1 5 5c0 4-5 9-5 9S0 9 0 5a5 5 0 0 1 5-5z"/></svg>Po. box 201, Street Name, City Name, Zip Code - 00000
  </div>
</section>

<!-- Business card, back -->
<section class="piece card card-back">
  <div class="ring" style="left:76px;top:17px;width:48px;height:48px"></div>
  <div class="brand" style="left:0;width:200px;top:72px;font-size:7px;letter-spacing:1px">Harborline Realty</div>
  <div class="abs web"><span class="rule"></span>www.harborlinerealty.com<span class="rule"></span></div>
</section>

<!-- Envelope -->
<section class="envelope abs">
  <svg class="flap" width="542" height="80" viewBox="0 0 542 80">
    <path d="M0 72 Q2 48 16 42 L250 2 Q272 -2 294 2 L526 40 Q540 46 542 72 Z" fill="#f2f2f2"/>
  </svg>
  <div class="ring" style="left:254px;top:18px;width:32px;height:32px;border-width:2.5px;z-index:1"></div>
  <div class="front">
    <div class="ring" style="left:74px;top:9px;width:42px;height:42px"></div>
    <div class="brand" style="left:38px;top:56px;width:114px;font-size:11px;letter-spacing:1px">Harborline<br>
      <span style="font-size:7.5px;letter-spacing:2.5px"><span class="rule" style="width:16px;margin-right:3px"></span>Realty<span class="rule" style="width:16px;margin-left:3px"></span></span>
    </div>
    <div class="abs address">
      <svg width="8" height="11" viewBox="0 0 10 14" style="fill:var(--navy);margin-top:2px"><path d="M5 0a5 5 0 0 1 5 5c0 4-5 9-5 9S0 9 0 5a5 5 0 0 1 5-5zm0 3a2 2 0 1 0 0 4 2 2 0 0 0 0-4z"/></svg>
      <div>Po. box 201, Street Name,<br>City Name, Zip Code - 00000</div>
    </div>
    <div class="band" style="top:207px"></div>
    <div class="seal" style="left:469px;top:189px;width:42px;height:42px"></div>
  </div>
</section>

</body>
</html>
```